Indy Film Production Company/Studio

We need a business card designed from an existing logo. We are a digital studio/production company that caters to creating genre entertainment, like Action, Horror, and martial arts. The card along with the logo will be used to Brand the company from letter heads to banners. The design will also be used for postcards and Brochures. It should be professional and masculine.
Updates

Thank you to all the designers who have participated. I'm narrowing down who it will be. Thank you again.

Target Market(s)

Investors, Networks, Producers, and actors

Industry/Entity Type

Film Production

Contact Information for Business Card

Teodoro Valbuena
Producer/Writer/Director
www.kestrelpicturehouse.example

Requirements
Must have
• Website address, Facebook icon and Twitter icon possibly in the back of the card.
Nice to have
• Logline of Company: Follow The Action.

```html
<!DOCTYPE html>
<html lang="en">
<head>
<meta charset="utf-8">
<title>Kestrel Picture House — Business Card</title>
<link href="https://fonts.googleapis.com/css2?family=Arimo:wght@400;700&display=swap" rel="stylesheet">
<style>
  :root {
    --page-bg: #e4e4e4;
    --brand-red: #e31b23;
    --brand-red-deep: #b5141b;
    --ink: #1f1f1f;
    --ink-soft: #444444;
    --rule: #c9c9c9;
    --swoosh: #2b2b2b;
    --card-white: #ffffff;
    --social-grey: #6a6a6a;
  }
  * { box-sizing: border-box; margin: 0; padding: 0; }
  html, body {
    width: 1200px; height: 950px; overflow: hidden;
    background: var(--page-bg);
    font-family: "Arimo", Arial, sans-serif;
  }
  .sheet {
    width: 1200px; height: 950px;
    display: flex; flex-direction: column; align-items: center; justify-content: center;
    gap: 40px;
  }
  .card {
    position: relative;
    width: 720px; height: 412px;
    border-radius: 4px;
    overflow: hidden;
    box-shadow: 0 6px 18px rgba(0,0,0,0.18);
  }

  /* Back of card */
  .card--back {
    background: linear-gradient(135deg, var(--brand-red) 0%, var(--brand-red-deep) 100%);
    color: var(--card-white);
    display: flex; flex-direction: column; align-items: center; justify-content: center;
  }
  .card--back .wordmark {
    font-weight: 700; font-size: 46px; letter-spacing: 1px;
    text-transform: uppercase; color: var(--card-white);
  }
  .card--back .site {
    margin-top: 18px; font-size: 20px; letter-spacing: 2px; color: var(--card-white);
  }
  .card--back .social { position: absolute; top: 22px; right: 24px; }
  .card--back .social__tile { background: var(--card-white); }

  .social { display: flex; gap: 4px; }
  .social__tile { width: 24px; height: 24px; background: var(--social-grey); }

  /* Front of card */
  .card--front { background: var(--card-white); }
  .card--front .wave { position: absolute; inset: 0; width: 100%; height: 100%; }
  .contact {
    position: absolute; left: 44px; top: 96px;
  }
  .contact__name { color: var(--brand-red); font-size: 24px; font-weight: 400; }
  .contact__role { color: var(--ink); font-size: 19px; margin-top: 4px; padding-bottom: 8px;
    border-bottom: 1px solid var(--rule); width: 250px; }
  .contact__list { list-style: none; margin-top: 8px; }
  .contact__item {
    display: flex; align-items: center; gap: 8px;
    font-size: 17px; color: var(--ink-soft); line-height: 25px;
  }
  .contact__icon { width: 14px; height: 14px; flex: none; }
  .card--front .wordmark {
    position: absolute; right: 40px; top: 110px; width: 290px;
    text-align: center; color: var(--brand-red);
    font-weight: 700; font-size: 32px; line-height: 1.1; text-transform: uppercase;
  }
  .card--front .divider {
    position: absolute; left: 44px; right: 40px; top: 262px;
    border-top: 1px solid var(--rule);
  }
  .card--front .social { position: absolute; right: 40px; top: 280px; }
</style>
</head>
<body>
<main class="sheet">

  <section class="card card--back" aria-label="Card back">
    <div class="social" aria-label="Social profiles">
      <span class="social__tile" role="img" aria-label="Social profile"></span>
      <span class="social__tile" role="img" aria-label="Social profile"></span>
    </div>
    <div class="wordmark">Kestrel Picture House</div>
    <div class="site">www.kestrelpicturehouse.example</div>
  </section>

  <section class="card card--front" aria-label="Card front">
    <svg class="wave" viewBox="0 0 720 412" preserveAspectRatio="none" aria-hidden="true">
      <path d="M0 272 C 180 300, 360 350, 520 372 C 610 384, 680 384, 720 380 L720 412 L0 412 Z" fill="var(--brand-red)"/>
      <path d="M0 258 C 170 282, 350 330, 520 356 C 610 368, 680 372, 720 372 L720 380 C 680 384, 610 384, 520 372 C 360 350, 180 300, 0 272 Z" fill="var(--swoosh)"/>
    </svg>

    <div class="contact">
      <h1 class="contact__name">Teodoro Valbuena</h1>
      <p class="contact__role">Producer/Writer/Director</p>
      <ul class="contact__list">
        <li class="contact__item">
          <svg class="contact__icon" viewBox="0 0 14 14" aria-hidden="true"><path d="M3 1 L5 1 L6 4 L4.5 5.5 C5.5 7.5 6.5 8.5 8.5 9.5 L10 8 L13 9 L13 11 C13 12 12 13 11 13 C6 13 1 8 1 3 C1 2 2 1 3 1 Z" fill="var(--brand-red)"/></svg>
          555 0142 7788
        </li>
        <li class="contact__item">
          <svg class="contact__icon" viewBox="0 0 14 14" aria-hidden="true"><rect x="1" y="3" width="12" height="8" fill="var(--brand-red)"/><path d="M1 3 L7 8 L13 3" stroke="#fff" stroke-width="1.2" fill="none"/></svg>
          teodoro@kestrel.example
        </li>
        <li class="contact__item">
          <svg class="contact__icon" viewBox="0 0 14 14" aria-hidden="true"><path d="M7 1 C4.2 1 2.5 3 2.5 5.3 C2.5 8.5 7 13 7 13 C7 13 11.5 8.5 11.5 5.3 C11.5 3 9.8 1 7 1 Z" fill="var(--brand-red)"/><circle cx="7" cy="5.3" r="1.7" fill="#fff"/></svg>
          www.kestrelpicturehouse.example
        </li>
      </ul>
    </div>

    <div class="wordmark">Kestrel Picture House</div>
    <div class="divider"></div>
    <div class="social" aria-label="Social profiles">
      <span class="social__tile" role="img" aria-label="Social profile"></span>
      <span class="social__tile" role="img" aria-label="Social profile"></span>
    </div>
  </section>

</main>
</body>
</html>
```